Weightloss company needs Business Card

We want a business card that is clean and professional, yet portrays that we are a friendly, innovative, and versatile program designed to fit the needs of our clients.
I would like there to be 2 sides, one side having an appointment card, and the other side containing the logo and business information. There can be decorations on both sides. The logo is attached.

Target Market(s)

Men and women 40-60

Industry/Entity Type

Business

Contact Information for Business Card

Font styles to use
Sans Serif

Requirements
Must have
• The logo, space for business information
Nice to have
• The colors in the logo
Should not have
• No pictures of people or food

```html
<!DOCTYPE html>
<html lang="en">
<head>
<meta charset="utf-8">
<title>Brightpath Wellness – Business Card</title>
<link rel="stylesheet" href="https://fonts.googleapis.com/css2?family=Open+Sans:wght@400;600;700&display=swap">
<style>
  :root {
    --backdrop: #ecebe9;
    --card-navy: #1f2a35;
    --brand-pink: #e8174f;
    --text-white: #ffffff;
    --slip-white: #ffffff;
    --dot-ink: #1f2a35;
  }
  * { margin: 0; padding: 0; box-sizing: border-box; }
  html, body {
    width: 1200px; height: 900px; overflow: hidden;
    background: var(--backdrop);
    font-family: "Open Sans", Arial, sans-serif;
  }
  .canvas { position: relative; width: 1200px; height: 900px; }

  .card {
    position: absolute;
    background: var(--card-navy);
    box-shadow: 0 6px 18px rgba(0,0,0,0.25);
  }
  .card--front { left: 238px; top: 62px; width: 555px; height: 342px; }
  .card--back  { left: 457px; top: 518px; width: 560px; height: 344px; }

  .brand {
    position: absolute;
    display: flex; align-items: center; gap: 8px;
    color: var(--brand-pink);
    font-weight: 700;
    white-space: nowrap;
  }
  .brand__dot {
    width: 10px; height: 10px; border-radius: 50%;
    background: var(--brand-pink);
    flex: none;
  }
  .brand__name { display: block; text-align: right; }
  .card--front .brand { left: 66px; top: 138px; font-size: 24px; line-height: 28px; }
  .card--back .brand  { left: 0; right: 0; top: 38px; justify-content: center; font-size: 30px; line-height: 32px; }

  .contact {
    position: absolute; left: 292px; top: 88px;
    color: var(--text-white);
    font-size: 15px; line-height: 20px;
  }
  .contact__name { font-size: 18px; font-weight: 600; line-height: 22px; }
  .contact__role { margin-bottom: 14px; }
  .contact__address { margin-bottom: 14px; }
  .contact__line { display: flex; align-items: center; gap: 8px; }
  .contact__line svg { width: 12px; height: 12px; fill: var(--text-white); flex: none; }

  .appointment {
    position: absolute; left: 33px; top: 138px; width: 495px; height: 186px;
    background: var(--slip-white);
    color: var(--brand-pink);
    font-weight: 600;
  }
  .appointment__title {
    position: absolute; top: 20px; left: 0; right: 0;
    text-align: center; font-size: 21px;
  }
  .appointment__field {
    position: absolute; left: 68px;
    display: flex; align-items: flex-end;
    font-size: 14px;
  }
  .appointment__field--name { top: 66px; }
  .appointment__field--date { top: 107px; }
  .appointment__blank {
    display: inline-block; height: 14px;
    border-bottom: 2px dotted var(--dot-ink);
    margin-left: 4px;
  }
  .appointment__note {
    position: absolute; top: 149px; left: 0; right: 0;
    text-align: center; font-size: 14px;
  }
</style>
</head>
<body>
<div class="canvas">

  <section class="card card--front">
    <div class="brand"><span class="brand__dot"></span><span class="brand__name">Brightpath<br>Wellness</span></div>

    <div class="contact">
      <p class="contact__name">Daniel Reeves</p>
      <p class="contact__role">Managing Director</p>
      <p class="contact__address">12345, Address Goes Here<br>Country Name, 123456.</p>
      <p class="contact__line">
        <svg viewBox="0 0 24 24"><path d="M6.6 10.8a15.2 15.2 0 0 0 6.6 6.6l2.2-2.2a1 1 0 0 1 1-.25 11.4 11.4 0 0 0 3.6.57 1 1 0 0 1 1 1V20a1 1 0 0 1-1 1A17 17 0 0 1 3 4a1 1 0 0 1 1-1h3.5a1 1 0 0 1 1 1c0 1.25.2 2.45.57 3.57a1 1 0 0 1-.25 1z"/></svg>
        044-123 456 789
      </p>
      <p class="contact__line">
        <svg viewBox="0 0 24 24"><path d="M2 5h20v14H2z M2 5l10 8 10-8" fill="none" stroke="#fff" stroke-width="2"/><path d="M2 5h20L12 12z"/></svg>
        info@webname.com
      </p>
      <p class="contact__line">
        <svg viewBox="0 0 24 24"><circle cx="12" cy="12" r="10"/><path d="M3 12h18M12 2c3 3 3 17 0 20M12 2c-3 3-3 17 0 20" stroke="#1f2a35" stroke-width="1.5" fill="none"/></svg>
        www.websitename.com
      </p>
    </div>
  </section>

  <section class="card card--back">
    <div class="brand"><span class="brand__dot"></span><span class="brand__name">Brightpath<br>Wellness</span></div>

    <div class="appointment">
      <h2 class="appointment__title">Your Next Appointment is</h2>
      <p class="appointment__field appointment__field--name">Name:<span class="appointment__blank" style="width:308px"></span></p>
      <p class="appointment__field appointment__field--date">Date:<span class="appointment__blank" style="width:166px"></span>&nbsp;Time:<span class="appointment__blank" style="width:110px"></span></p>
      <p class="appointment__note">If unable to keep appointment,&nbsp; kindly give 24hrs notice.</p>
    </div>
  </section>

</div>
</body>
</html>
```